Social media app sign-up flow that asks users to give personal info and connect with other apps

Design an interactive, fun, and playful sign-up flow in which you are providing information about you, your interests, and connecting with different API plug-ins such as Chatterloop, Workvine, Tunevale, etc. (using the brand palette attached).

Basic wireframe, and business requirements are also attached.

Target Market(s)

Gen Z + Millennials (ages 22-40)

Font styles to use
Sans Serif

Colors
fbed22
fbee3d
fbf289

Requirements
Must have
• Forms for users to submit their info. Follow the color palette attached.

Connect with Chatterloop, Connect with Workvine, Connect with Tunevale, Connect with Gatherpost buttons
Nice to have
• I like the way you can use cards to submit your information for each category. Interactive card design for providing your info
Should not have
• Basic outdated designs, long forms

```html
<!DOCTYPE html>
<html lang="en">
<head>
<meta charset="utf-8">
<title>Sign-up flow</title>
<link href="https://fonts.googleapis.com/css2?family=IBM+Plex+Sans:wght@400;500;600;700&display=swap" rel="stylesheet">
<style>
:root{
  --bg:#8a8a8a; --panel:#f7f6f4; --ink:#1e1e1e; --muted:#555;
  --yellow:#fdc52f; --tile:#5c6579; --line:#bdbdbd;
  --email:#5a5859; --chatter:#46619c; --search:#f15a24; --orchard:#948b8b;
  --workvine:#0077b5; --tunevale:#1db954; --white:#fff;
}
*{box-sizing:border-box;margin:0;padding:0}
html,body{width:728px;height:1200px;overflow:hidden;background:var(--bg);font-family:"IBM Plex Sans",sans-serif;color:var(--ink)}
.screen{position:absolute;width:301px;height:536px;background:var(--panel)}
.title{position:absolute;left:0;right:0;text-align:center;font-size:19px;font-weight:400}
.field{position:absolute;left:23px;width:257px;height:34px;background:var(--white);border:1px solid #aaa;font-size:9.5px;padding-left:13px;display:flex;align-items:center}
.caret{position:absolute;right:12px;top:14px;width:0;height:0;border-left:3.5px solid transparent;border-right:3.5px solid transparent;border-top:4px solid #222}
.helper{position:absolute;left:23px;top:176px;font-size:9px;line-height:12px;color:var(--muted)}
.continue{position:absolute;left:23px;top:214px;width:257px;height:37px;background:var(--yellow);color:var(--white);font-weight:700;font-size:15px;letter-spacing:.5px;display:flex;align-items:center;justify-content:center}
.divider{position:absolute;left:23px;top:303px;width:257px;height:1px;background:var(--line)}
.or{position:absolute;left:138px;top:290px;width:26px;height:26px;border-radius:50%;border:1.5px solid var(--line);background:var(--panel);font-size:9px;display:flex;align-items:center;justify-content:center}
.social{position:absolute;left:23px;width:257px;height:34px;color:var(--white);font-size:9px;font-weight:700;letter-spacing:.2px;display:flex;align-items:center;padding-left:39px}
.social .mark{position:absolute;left:14px;top:11px;width:12px;height:12px}
.tile{position:absolute;width:120px;height:98px;background:var(--tile);color:var(--white);font-size:10.5px;font-weight:500;letter-spacing:.3px;line-height:14px;text-align:center;text-transform:uppercase}
.tile svg{position:absolute;left:45px;top:14px;width:30px;height:32px}
.tile span{position:absolute;left:0;right:0;top:58px}
.card{position:absolute;left:23px;top:128px;width:256px;height:200px;background:var(--white);box-shadow:0 1px 4px rgba(0,0,0,.08)}
.chip{position:absolute;width:104px;height:32px;border:1px solid #999;font-size:10.5px;padding-left:9px;display:flex;align-items:center;white-space:nowrap}
.chip i{position:absolute;right:6px;top:9px;width:13px;height:13px;border-radius:50%;background:#9a9a9a}
.chip i::before,.chip i::after{content:"";position:absolute;left:3px;top:6px;width:7px;height:1.5px;background:var(--white);transform:rotate(45deg)}
.chip i::after{transform:rotate(-45deg)}
.typing{position:absolute;left:19px;top:108px;width:218px;height:32px;border:1px solid #999;font-size:11px;padding-left:10px;display:flex;align-items:center}
.typing b{display:inline-block;width:1px;height:17px;background:#999;margin-left:4px}
.suggest{position:absolute;left:19px;top:139px;width:218px;height:37px;border:1px solid #999;border-top:none;font-size:9px;padding-left:10px;display:flex;align-items:center}
.connect{position:absolute;left:24px;width:255px;height:41px;color:var(--white);font-size:11.5px;letter-spacing:.2px;display:flex;align-items:center;padding-left:66px;white-space:nowrap}
.connect::before{content:"";position:absolute;left:52px;top:0;bottom:0;width:2px;background:rgba(255,255,255,.2)}
.connect .dot{position:absolute;left:19px;top:13px;width:14px;height:14px;border-radius:50%;background:var(--white)}
</style>
</head>
<body>

<section class="screen" style="left:44px;top:68px">
  <h1 class="title" style="top:31px">Sign Up</h1>
  <div class="field" style="top:90px">COUNTRY / REGION<span class="caret"></span></div>
  <div class="field" style="top:135px">PHONE NUMBER</div>
  <p class="helper">We'll call or text you to confirm your number.<br>Standard message and date rates apply.</p>
  <div class="continue">CONTINUE</div>
  <div class="divider"></div><div class="or">OR</div>
  <div class="social" style="top:350px;background:var(--email)">
    <svg class="mark" viewBox="0 0 12 12"><rect x="0" y="2" width="12" height="8" fill="#fff"/><path d="M0 2l6 4 6-4" stroke="#5a5859" stroke-width="1.2" fill="none"/></svg>CONTINUE WITH EMAIL</div>
  <div class="social" style="top:392px;background:var(--chatter)"><svg class="mark" viewBox="0 0 12 12"><rect x="2" y="2" width="8" height="8" fill="#fff"/></svg>CONTINUE WITH CHATTERLOOP</div>
  <div class="social" style="top:434px;background:var(--search)"><svg class="mark" viewBox="0 0 12 12"><rect x="2" y="2" width="8" height="8" fill="#fff"/></svg>CONTINUE WITH SEARCHLY</div>
  <div class="social" style="top:476px;background:var(--orchard)"><svg class="mark" viewBox="0 0 12 12"><rect x="2" y="2" width="8" height="8" fill="#fff"/></svg>CONTINUE WITH ORCHARDLY</div>
</section>

<section class="screen" style="left:376px;top:68px">
  <h1 class="title" style="top:28px">Tell me about you</h1>
  <div class="tile" style="left:25px;top:82px"><svg viewBox="0 0 30 32" fill="none" stroke="#fdc52f" stroke-width="2"><path d="M15 30C8 21 4 16 4 11a11 11 0 0122 0c0 5-4 10-11 19z"/><circle cx="15" cy="11" r="4.5"/></svg><span>Places<br>I’ve lived</span></div>
  <div class="tile" style="left:157px;top:82px"><svg viewBox="0 0 30 32" fill="#fdc52f"><rect x="2" y="26" width="26" height="3"/><rect x="4" y="13" width="22" height="13"/><path d="M3 13l12-6 12 6z"/><rect x="14.5" y="1" width="1.5" height="6"/><g fill="#5c6579"><rect x="7" y="16" width="2" height="8"/><rect x="11" y="16" width="2" height="8"/><rect x="17" y="16" width="2" height="8"/><rect x="21" y="16" width="2" height="8"/></g></svg><span>Schools<br>I’ve lived</span></div>
  <div class="tile" style="left:25px;top:188px"><svg viewBox="0 0 30 32" fill="none" stroke="#fdc52f" stroke-width="2"><rect x="2" y="9" width="26" height="19" rx="2"/><path d="M10 9V5h10v4M2 17h26"/><rect x="13" y="15" width="4" height="5" fill="#5c6579"/></svg><span>Places<br>I’ve worked</span></div>
  <div class="tile" style="left:157px;top:188px"><svg viewBox="0 0 30 32" fill="none" stroke="#fdc52f" stroke-width="2"><circle cx="15" cy="15" r="13"/><circle cx="15" cy="12" r="5" fill="#fdc52f"/><path d="M6 24c3-5 15-5 18 0" fill="#fdc52f"/></svg><span>People I<br>know</span></div>
  <div class="tile" style="left:25px;top:296px"><svg viewBox="0 0 30 32" fill="none" stroke="#fdc52f" stroke-width="2"><rect x="3" y="5" width="24" height="22" rx="2"/><path d="M3 11h24M8 2v6M15 2v6M22 2v6"/><g fill="#fdc52f" stroke="none"><rect x="7" y="14" width="3" height="3"/><rect x="12" y="14" width="3" height="3"/><rect x="17" y="14" width="3" height="3"/><rect x="7" y="19" width="3" height="3"/><rect x="12" y="19" width="3" height="3"/><rect x="17" y="19" width="3" height="3"/></g></svg><span>Events I’ve<br>attended</span></div>
  <div class="tile" style="left:157px;top:296px"><svg viewBox="0 0 30 32" fill="#fdc52f"><ellipse cx="8" cy="12" rx="6" ry="7"/><ellipse cx="22" cy="12" rx="6" ry="7"/><ellipse cx="15" cy="8" rx="6" ry="7"/><path d="M8 19l5 11M22 19l-5 11M15 15v15" stroke="#fdc52f" stroke-width="1"/></svg><span>Events I’m<br>attending</span></div>
  <div class="tile" style="left:25px;top:405px"><svg viewBox="0 0 30 32" fill="none" stroke="#fdc52f" stroke-width="2"><path d="M11 25V8l14-4v17"/><circle cx="7.5" cy="25" r="3.5"/><circle cx="21.5" cy="21" r="3.5"/></svg><span>Music I<br>love</span></div>
  <div class="tile" style="left:157px;top:405px"><svg viewBox="0 0 30 32" fill="#fdc52f"><circle cx="7" cy="7" r="3"/><circle cx="15" cy="5" r="3"/><circle cx="23" cy="7" r="3"/><rect x="3" y="11" width="8" height="13" rx="2"/><rect x="11" y="9" width="8" height="19" rx="2"/><rect x="19" y="11" width="8" height="13" rx="2"/></svg><span>Teams I<br>love</span></div>
</section>

<section class="screen" style="left:44px;top:630px">
  <h1 class="title" style="top:74px">Places I’ve Lived</h1>
  <div class="card">
    <div class="chip" style="left:19px;top:20px">Chicago<i></i></div>
    <div class="chip" style="left:134px;top:20px">Madrid<i></i></div>
    <div class="chip" style="left:19px;top:63px">Paris<i></i></div>
    <div class="chip" style="left:134px;top:63px">Rio de Janiero<i></i></div>
    <div class="typing">London<b></b></div>
    <div class="suggest"><strong>London,</strong>&nbsp;United Kingdom</div>
  </div>
  <div class="connect" style="top:354px;background:var(--chatter)"><span class="dot"></span>CONNECT WITH CHATTERLOOP</div>
  <div class="connect" style="top:408px;background:var(--workvine)"><span class="dot"></span>CONNECT WITH WORKVINE</div>
</section>

<section class="screen" style="left:376px;top:631px">
  <h1 class="title" style="top:74px">Music I Love</h1>
  <div class="card">
    <div class="chip" style="left:19px;top:20px">The Lanterns<i></i></div>
    <div class="chip" style="left:134px;top:20px">Marisol<i></i></div>
    <div class="chip" style="left:19px;top:63px">Nine Dimes<i></i></div>
    <div class="chip" style="left:134px;top:63px">Ray Calder<i></i></div>
    <div class="typing">Brittany Spar<b></b></div>
    <div class="suggest"><strong>Brittany Sparrow</strong></div>
  </div>
  <div class="connect" style="top:354px;background:var(--chatter)"><span class="dot"></span>CONNECT WITH CHATTERLOOP</div>
  <div class="connect" style="top:408px;background:var(--tunevale)"><span class="dot"></span>CONNECT WITH TUNEVALE</div>
</section>

</body>
</html>
```